Telecommunications/Power civil contractor needs business card design

Were a new telecommunications/power underground civil contractor that is looking for a new business card design. Our company colours are silver or grey and orange. Feel free to use the white background logo or the black background logo.

Target Market(s)

Local contractors, utility companies, private sector mining/energy companies, developers.

Industry/Entity Type

Telecommunications

Contact Information for Business Card

Each card will need the following info:
Persons name:
Title:
E-mail:
Phone number:
Shop Address:
Mailing Address:

Requirements
Must have
• Each card will need the following info:
• Persons name:
• Title:
• E-mail:
• Phone number:
• Shop Address:
• Mailing Address:

```html
<!DOCTYPE html>
<html lang="en">
<head>
<meta charset="utf-8">
<title>Ridgeline Civil Inc — Business Card</title>
<link href="https://fonts.googleapis.com/css2?family=Lato:wght@400;700;900&display=swap" rel="stylesheet">
<style>
  :root {
    --backdrop: #1b1b1c;
    --card-dark: #1f2022;
    --card-dark-2: #2c2d30;
    --card-light: #f1f1f1;
    --card-light-2: #d9d9d9;
    --orange: #d4541c;
    --text-light: #ffffff;
    --text-muted: #d8d8d8;
    --logo-grey: #5a5b5e;
  }
  * { margin: 0; padding: 0; box-sizing: border-box; }
  html, body {
    width: 1200px; height: 873px; overflow: hidden;
    background: var(--backdrop);
    font-family: "Lato", Arial, sans-serif;
  }
  .canvas { position: relative; width: 1200px; height: 873px; }
  .card {
    position: absolute; left: 180px; top: 196px;
    width: 840px; height: 480px;
    overflow: hidden;
    box-shadow: 0 20px 50px rgba(0,0,0,0.6);
  }
  .card-art { position: absolute; inset: 0; }
  .identity {
    position: absolute; left: 60px; top: 120px;
    display: flex; align-items: center; color: var(--text-light);
  }
  .identity .name { font-weight: 700; font-size: 24px; }
  .identity .divider {
    width: 2px; height: 30px; background: var(--orange); margin: 0 12px;
  }
  .identity .title { font-size: 15px; color: var(--text-muted); }
  .contacts { position: absolute; left: 60px; top: 196px; list-style: none; }
  .contacts li {
    display: flex; align-items: center; gap: 14px;
    color: var(--text-muted); font-size: 15px; margin-bottom: 14px;
  }
  .contacts svg { width: 18px; height: 18px; fill: var(--orange); flex: none; }
  .address {
    position: absolute; left: 60px; color: var(--text-muted);
    font-size: 16px; line-height: 1.3;
  }
  .address .label { color: var(--orange); }
  .address.shop { top: 290px; }
  .address.mailing { top: 370px; }
  .brand {
    position: absolute; left: 560px; top: 190px;
    display: flex; align-items: center; gap: 14px;
  }
  .brand .mark {
    width: 44px; height: 44px; border-radius: 50%;
    border: 4px solid var(--orange); flex: none;
  }
  .brand .name {
    font-weight: 900; font-size: 26px; line-height: 1.05;
    color: var(--logo-grey); letter-spacing: 1px; text-transform: uppercase;
  }
</style>
</head>
<body>
<main class="canvas">
  <section class="card">
    <svg class="card-art" viewBox="0 0 840 480" width="840" height="480">
      <defs>
        <linearGradient id="dark-panel" x1="0" y1="0" x2="1" y2="1">
          <stop offset="0" stop-color="var(--card-dark-2)"/>
          <stop offset="1" stop-color="var(--card-dark)"/>
        </linearGradient>
        <linearGradient id="light-panel" x1="0" y1="0" x2="1" y2="1">
          <stop offset="0" stop-color="var(--card-light)"/>
          <stop offset="1" stop-color="var(--card-light-2)"/>
        </linearGradient>
      </defs>
      <rect class="faceted-texture" role="img" aria-label="Dark low-poly faceted texture" width="840" height="480" fill="url(#dark-panel)"/>
      <polygon class="light-panel" points="520,0 840,0 840,480 350,480" fill="url(#light-panel)"/>
      <polygon class="accent-stripe" points="548,0 557,0 392,480 378,480" fill="var(--orange)"/>
    </svg>

    <div class="identity">
      <span class="name">Daniel Whitcombe</span>
      <span class="divider"></span>
      <span class="title">Chief Operating Officer</span>
    </div>

    <ul class="contacts">
      <li>
        <svg viewBox="0 0 24 24" aria-hidden="true"><path d="M6.6 10.8a15.1 15.1 0 0 0 6.6 6.6l2.2-2.2a1 1 0 0 1 1-.25 11.4 11.4 0 0 0 3.6.57 1 1 0 0 1 1 1V20a1 1 0 0 1-1 1A17 17 0 0 1 3 4a1 1 0 0 1 1-1h3.5a1 1 0 0 1 1 1c0 1.25.2 2.45.57 3.57a1 1 0 0 1-.25 1z"/></svg>
        412-555-0147
      </li>
      <li>
        <svg viewBox="0 0 24 24" aria-hidden="true"><path d="M2 5h20v14H2z M2 5l10 8 10-8" /></svg>
        enquiries@ridgelinecivil.com
      </li>
    </ul>

    <div class="address shop">
      <div class="label">(Shop Address)</div>
      <div>48 Harlow Lane,</div>
      <div>Fairbrook, PA 15099</div>
    </div>

    <div class="address mailing">
      <div class="label">(Mailing Address)</div>
      <div>#1120 Corwin Street,</div>
      <div>Eastvale, New York</div>
    </div>

    <div class="brand">
      <span class="mark"></span>
      <span class="name">Ridgeline<br>Civil Inc</span>
    </div>
  </section>
</main>
</body>
</html>
```